Alaska Law Firm Needs a Sticker Design

We need a design for stickers to put on already-printed brochures. We mail the brochures to potential clients so they can learn more about accident-induced injuries, insurance claims, legal representation, and our own law firm.

One of our lawyers wrote a book that provides a helpful overview of personal injury claims. We are offering this book for free to anyone who calls and requests it. Therefore, the sticker design should include one of the following phrases, or something very similar:
a) "Still have questions? Call and request our book-- for free!"
b) "Still have questions about auto accident claims? Call and request our book today."
c) "Still have questions about filing a claim? Call and request a free copy of our book."
d) "Still have questions? Call us today to request a free copy of our book, Clear Lanes Ahead."
e) "To learn more about automobile accidents and insurance, call today and request a free copy of our book."

The sticker should be approximately 3"x3" and may be a circle, square, rectangle, or ellipsis. The sticker will be placed on the back of the folder, which is light blue. We would like the sticker to match the color scheme of our website and the folder.

I will upload an image of the book cover as soon as I obtain it.

Law Firm

Font styles to use
Serif
Sans Serif

Requirements
Should not have
• Bright colors that aren't already used in the folder design. e.g. no bright orange, pink, chartreuse, turquoise, yellow, red.

```html
<!DOCTYPE html>
<html lang="en">
<head>
<meta charset="utf-8">
<title>Free Book Sticker</title>
<link href="https://fonts.googleapis.com/css2?family=Noto+Sans:wght@400;500;700&display=swap" rel="stylesheet">
<style>
  :root {
    --page-bg: #e8e9ea;
    --navy: #0f3a66;
    --deep-navy: #0a2f57;
    --slate: #5c5c5e;
    --muted-gray: #6a6c6e;
    --white: #ffffff;
    --cyan-light: #2ee2f7;
    --cyan-mid: #08c9e4;
    --cyan-edge: #00a9c8;
  }
  html, body {
    margin: 0;
    padding: 0;
    width: 1200px;
    height: 1200px;
    overflow: hidden;
    background: var(--page-bg);
  }
  .sticker {
    display: block;
    width: 1200px;
    height: 1200px;
    font-family: "Noto Sans", Verdana, sans-serif;
  }
  .ring-gray { fill: var(--slate); }
  .ring-navy { fill: var(--deep-navy); }
  .ring-white { fill: var(--white); }
  .text-navy { fill: var(--navy); }
  .text-white { fill: var(--white); }
  .text-gray { fill: var(--muted-gray); }
  .w-regular { font-weight: 400; }
  .w-medium { font-weight: 500; }
  .w-bold { font-weight: 700; }
  .call-icon { fill: var(--navy); }
  .call-label { fill: var(--white); font-weight: 400; }
</style>
</head>
<body>
<svg class="sticker" viewBox="0 0 1200 1200" xmlns="http://www.w3.org/2000/svg" aria-label="Sticker: to learn more about automobile accidents and insurance, call today and request a free copy of our book">
  <defs>
    <radialGradient id="sticker-face" cx="0.55" cy="0.5" r="0.55">
      <stop offset="0" stop-color="var(--cyan-light)"/>
      <stop offset="0.7" stop-color="var(--cyan-mid)"/>
      <stop offset="1" stop-color="var(--cyan-edge)"/>
    </radialGradient>
  </defs>

  <!-- layered rings -->
  <circle class="ring-gray" cx="600" cy="570" r="495"/>
  <circle class="ring-navy" cx="650" cy="610" r="495"/>
  <circle class="ring-white" cx="565" cy="640" r="490"/>
  <circle cx="615" cy="615" r="465" fill="url(#sticker-face)"/>

  <!-- message -->
  <text x="334" y="375" class="text-navy">
    <tspan class="w-regular" font-size="58">"To learn </tspan><tspan class="w-bold" font-size="82">more</tspan>
  </text>
  <text x="280" y="456">
    <tspan class="text-navy w-bold" font-size="82">about </tspan><tspan class="text-gray w-regular" font-size="58">automobile</tspan>
  </text>
  <text x="262" y="550">
    <tspan class="text-white w-medium" font-size="108" letter-spacing="-2">accidents </tspan><tspan class="text-navy w-regular" font-size="54">and</tspan>
  </text>
  <text x="381" y="641" class="text-navy w-medium" font-size="100" letter-spacing="-1">insurance,</text>
  <text x="389" y="717">
    <tspan class="text-white w-regular" font-size="64" letter-spacing="-1">today </tspan><tspan class="text-gray w-regular" font-size="56">and request</tspan>
  </text>
  <text x="402" y="798" class="text-gray w-regular" font-size="68">a free copy</text>
  <text x="276" y="898" class="text-navy w-bold" font-size="84" letter-spacing="-1">of our book."</text>

  <!-- call icon -->
  <g class="call-badge">
    <path class="call-icon" d="M262 580c-14 6-24 22-22 42 4 38 30 70 62 88 16 9 34 6 42-6l8-12c4-6 2-14-4-18l-22-14c-6-4-14-2-18 4l-6 9c-20-10-36-30-42-52l9-5c6-4 8-12 5-18l-12-23c-4-7-12-10-19-6z"/>
    <rect class="call-icon" x="232" y="700" width="162" height="60" rx="10"/>
    <text x="313" y="748" text-anchor="middle" class="call-label" font-size="54">call</text>
  </g>
</svg>
</body>
</html>
```